Local massage therapist needs some new marketing material

Hi there! I am a massage therapist here in Denver, CO in Alder Bend(shopping and art district) of the city. My business is called Lumo Bodywork of Denver. My practice has an eastern influence and I do reflexology, thai massage and use Chinese herbs, etc. I know all my clients and pay close attention to details. I am also very respectful of tradition and it shows in how I work. I tend to like modern, clean, fun, Asian designs. I am wanting a new business card and brochure. I have a logo and branding for my business that I want used in the design. Currently, the sign for my building is purple and I think my logo was designed to be purple. I will attach pictures of it and can send whatever files are necessary so it can be integrated into the brochure, etc. I like the purple but open to using other colors as well. Thanks!
My website is lumobodyworkofdenver.example where info can be gathered about me and services/fees for brochure.
Updates

Just increased budget. Please see new feedback in discussion thread.

Thanks!

                                       HEY ALL,

Just wanted to let you know that I made a change to my website. It is on the Prices Page. I no longer have the frequent  flyer prices but I added discounts. Let me know if you have any questions. Thanks so much!

Target Market(s)

healthy, urban, educated, upper middle class, yogis

Industry/Entity Type

Marketing

Requirements
Must have
• logo stays purple
Should not have
• not too busy

```html
<!DOCTYPE html>
<html lang="en">
<head>
<meta charset="utf-8">
<title>Lumo Bodywork of Denver – Trifold Brochure</title>
<link href="https://fonts.googleapis.com/css2?family=Open+Sans:ital,wght@0,400;0,600;1,600;1,700&display=swap" rel="stylesheet">
<style>
  :root {
    --purple: #652d90;
    --purple-line: #7a44a5;
    --orange: #f7941d;
    --ink: #231f20;
    --white: #ffffff;
    --page: #e4e5e7;
    --skin-deep: #b97a57;
    --skin-light: #e8c2a6;
    --foot-light: #f6e3d6;
  }
  * { margin: 0; padding: 0; box-sizing: border-box; }
  html, body { width: 1200px; height: 950px; overflow: hidden; }
  body {
    background: var(--page);
    font-family: "Open Sans", Arial, sans-serif;
    color: var(--white);
  }
  .brochure {
    position: absolute;
    left: 30px; top: 33px;
    width: 1140px; height: 884px;
    background: var(--purple);
    overflow: hidden;
  }
  .brochure-shapes { position: absolute; inset: 0; }

  .panel-text { position: absolute; font-style: italic; font-weight: 600; }

  /* Benefits panel */
  .benefits { left: 32px; top: 20px; width: 330px; }
  .benefits-title { font-size: 28px; font-weight: 700; letter-spacing: 1px; margin-bottom: 8px; }
  .benefits-list { list-style: none; font-size: 17.5px; line-height: 21px; }
  .benefits-list li { position: relative; padding-left: 22px; margin-bottom: 15px; }
  .benefits-list li::before { content: "+"; position: absolute; left: 2px; font-style: normal; }

  /* Middle panel */
  .tagline { left: 380px; width: 381px; top: 410px; text-align: center; font-size: 23px; line-height: 37px; }
  .tagline-box {
    display: inline-block; margin-top: 6px; padding: 1px 10px;
    background: var(--white); color: var(--purple); font-size: 24px; line-height: 40px; width: 300px;
  }
  .wordmark {
    font-family: "Open Sans", Arial, sans-serif;
    font-style: normal; font-weight: 400; letter-spacing: 9px;
    color: var(--white);
  }
  .middle-wordmark { position: absolute; left: 380px; width: 381px; top: 610px; text-align: center; font-size: 42px; padding-left: 9px; }
  .phone-box {
    position: absolute; left: 459px; top: 679px; width: 223px; height: 38px;
    background: var(--white); color: var(--purple);
    display: flex; align-items: center; justify-content: center; gap: 10px;
    font-style: italic; font-weight: 600; font-size: 23px;
  }
  .contact { left: 380px; width: 381px; top: 736px; text-align: center; font-size: 18px; line-height: 32.5px; }
  .contact-row { display: flex; align-items: center; justify-content: center; gap: 8px; }
  .contact-row svg { flex: none; }

  /* Cover panel */
  .cover-headline { right: 35px; top: 616px; text-align: right; font-size: 23px; line-height: 37px; text-transform: uppercase; }
  .cover-brand { position: absolute; left: 800px; top: 735px; display: flex; align-items: center; gap: 16px; }
  .cover-brand-dot { width: 54px; height: 54px; border: 2px solid var(--white); border-radius: 50%; }
  .cover-brand .wordmark { font-size: 42px; }
  .cover-web { left: 761px; width: 379px; top: 832px; text-align: center; font-size: 18px; }
</style>
</head>
<body>
<main class="brochure">
  <svg class="brochure-shapes" width="1140" height="884" viewBox="0 0 1140 884" aria-hidden="false">
    <defs>
      <linearGradient id="massage-tones" x1="0" y1="0" x2="1" y2="1">
        <stop offset="0" stop-color="var(--skin-deep)"/>
        <stop offset="1" stop-color="var(--skin-light)"/>
      </linearGradient>
      <linearGradient id="foot-tones" x1="0" y1="1" x2="1" y2="0">
        <stop offset="0" stop-color="var(--skin-light)"/>
        <stop offset="1" stop-color="var(--foot-light)"/>
      </linearGradient>
    </defs>
    <line class="panel-fold" x1="380" y1="0" x2="380" y2="884" stroke="var(--purple-line)" stroke-width="1"/>
    <line class="panel-fold" x1="761" y1="0" x2="761" y2="884" stroke="var(--purple-line)" stroke-width="1"/>
    <polygon role="img" aria-label="Photo: hot stone massage, smooth black stones placed along a relaxed client's back" points="300,0 1140,0 1140,597" fill="url(#massage-tones)"/>
    <polygon points="287,0 300,0 1140,597 1140,606" fill="var(--ink)"/>
    <polygon points="276,0 287,0 1140,606 1140,614" fill="var(--orange)"/>
    <polygon role="img" aria-label="Photo: hands giving a reflexology foot massage" points="0,609 0,884 375,884" fill="url(#foot-tones)"/>
    <polygon points="0,597 0,609 375,884 392,884" fill="var(--ink)"/>
    <polygon points="0,588 0,597 392,884 404,884" fill="var(--orange)"/>
  </svg>

  <section class="panel-text benefits">
    <h2 class="benefits-title">BENEFITS</h2>
    <ul class="benefits-list">
      <li>Relaxing the whole body</li>
      <li>Loosening and relieving tired,<br>aching and tight muscles</li>
      <li>Increasing flexibility and range<br>of motion</li>
      <li>Diminishing chronic pain</li>
      <li>Calming the nervous system</li>
      <li>Lowering blood pressure and<br>heart rate</li>
      <li>Enhancing skin tone</li>
      <li>Aiding in recovery following<br>injuries and illness</li>
      <li>Strengthening the immune<br>system</li>
      <li>Reducing headaches and<br>mental stress</li>
      <li>Improving relaxation</li>
      <li>Promoting restful sleep</li>
    </ul>
  </section>

  <p class="panel-text tagline">May You Awaken<br>to The Light of<br><span class="tagline-box">Your Own True Nature</span></p>

  <div class="wordmark middle-wordmark">LUMO</div>
  <div class="phone-box">
    <svg width="16" height="20" viewBox="0 0 16 20" aria-hidden="true"><path d="M3 1 L6 1 L7 6 L5 8 Q7 12 10 14 L12 12 L15 14 L15 17 Q13 19 10 18 Q3 14 1 6 Q1 2 3 1 Z" fill="var(--purple)"/></svg>
    <span>303.555.0148</span>
  </div>
  <address class="panel-text contact">
    <div class="contact-row">
      <svg width="12" height="16" viewBox="0 0 12 16" aria-hidden="true"><path d="M6 0 A6 6 0 0 1 12 6 C12 10 6 16 6 16 C6 16 0 10 0 6 A6 6 0 0 1 6 0 Z M6 3.5 A2.5 2.5 0 1 0 6 8.5 A2.5 2.5 0 1 0 6 3.5 Z" fill="var(--white)" fill-rule="evenodd"/></svg>
      <span>1480 E Alder Ave,</span>
    </div>
    <div>Denver, CO 80206</div>
    <div class="contact-row">
      <svg width="18" height="13" viewBox="0 0 18 13" aria-hidden="true"><rect x="1" y="1" width="16" height="11" fill="none" stroke="var(--white)" stroke-width="1.6"/><path d="M1 1 L9 8 L17 1" fill="none" stroke="var(--white)" stroke-width="1.6"/></svg>
      <span>info@lumobodyworkofdenver.example</span>
    </div>
    <div class="contact-row">
      <svg width="16" height="16" viewBox="0 0 16 16" aria-hidden="true"><g fill="none" stroke="var(--white)" stroke-width="1.4"><circle cx="8" cy="8" r="7"/><ellipse cx="8" cy="8" rx="3" ry="7"/><line x1="1" y1="8" x2="15" y2="8"/></g></svg>
      <span>lumobodyworkofdenver.example</span>
    </div>
  </address>

  <p class="panel-text cover-headline">Your Path to Wellness<br>Begins Here!</p>
  <div class="cover-brand">
    <span class="cover-brand-dot"></span>
    <span class="wordmark">LUMO</span>
  </div>
  <p class="panel-text cover-web">lumobodyworkofdenver.example</p>
</main>
</body>
</html>
```